Brightway Haus Inc. Business Card Design

Brightway Haus Inc. is in search of a great clean design for our business cards!

Looking to incorporate our full logo and watermark on side one (however, I am open to having the text and watermark separated within the design.)

On side two, I am looking to have contact information (Name, Position, Phone #, Email, Website (www.thebrightwayhaus.ca). Can have the logo and/or watermark as part of the design if applicable.

Please add tagline "Where Shine Counts" on either side 1 or 2. This tagline can be in a sans serif, serif or cursive font as long as it compliments overall design. Capitalization can be title or sentence case depending on how it fits within the design.

Get creative!! Looking for a clean, crisp, premium design! Looking for a glossy card finish with spot UV features when printed. Cards will also be printed with rounded corners. Standard dimensions (3.5 x 2).

Target Market(s)

B2B - primary clients are business owners or property management corporations. (residential jobs are few and far between)

Industry/Entity Type

Business

Contact Information for Business Card

- clean, crisp design
- double sided
- spot UV accents and glossy finish upon printing
- standard business card size (3.5 x 2) with rounded corners
- please see project description for requirements per side

Font styles to use
Sans Serif

Requirements
Must have
• - adequate bleeds with print ready files
• - cohesive design elements between side 1 & 2
• - spot UV elements (can be on both sides or just one, use your discretion)
• - colour pallet should match the logo file provided
• - incorporate tagline "where shine counts" (this tagline can be in a serif or sans serif font as long as it is complimentary to the overall design.
Nice to have
• - Premium elements with a clean design
Should not have
• - Please omit cartoon or whimsical like designs, think premium.
• - Colours should not stray from the pallet of the provided logo.

```html
<!DOCTYPE html>
<html lang="en">
<head>
<meta charset="utf-8">
<title>Brightway Haus Inc. – Business Card</title>
<link rel="stylesheet" href="https://fonts.googleapis.com/css2?family=Open+Sans:wght@300;400;600;700;800&display=swap">
<style>
  :root {
    --teal: #0bb3b9;
    --navy: #1b2656;
    --white: #ffffff;
    --stage: #f1f4f3;
    --rule: rgba(255, 255, 255, 0.55);
    --accent: #2a9be0;
  }
  * { box-sizing: border-box; margin: 0; padding: 0; }
  html, body { width: 1200px; height: 750px; overflow: hidden; }
  body {
    background: var(--stage);
    font-family: "Open Sans", Arial, sans-serif;
    display: flex;
    align-items: center;
    justify-content: center;
    gap: 90px;
  }
  .card {
    position: relative;
    width: 320px;
    height: 560px;
    border-radius: 26px;
    overflow: hidden;
    box-shadow: 0 14px 30px rgba(27, 38, 86, 0.18);
  }

  /* Shared wordmark */
  .brand-name {
    display: inline-flex;
    align-items: center;
    gap: 8px;
    white-space: nowrap;
    font-weight: 800;
    font-size: 20px;
    letter-spacing: 0.4px;
    text-transform: uppercase;
    color: var(--white);
  }
  .brand-name__mark {
    width: 12px; height: 12px;
    flex: none;
    background: currentColor;
  }

  /* Side one */
  .card--front { background: var(--teal); }
  .front__brand {
    position: absolute;
    top: 165px; left: 0; right: 0;
    display: flex;
    flex-direction: column;
    align-items: center;
  }
  .front__tagline {
    margin-top: 6px;
    font-size: 14px;
    color: var(--navy);
    letter-spacing: 0.4px;
  }
  .front__footer {
    position: absolute;
    left: 0; right: 0; bottom: 0;
    height: 135px;
    background: var(--navy);
    display: flex;
    align-items: center;
    justify-content: center;
  }
  .front__web {
    font-size: 14px;
    letter-spacing: 0.6px;
    color: var(--teal);
  }

  /* Side two */
  .card--back { background: var(--navy); }
  .back__head {
    position: absolute;
    top: 0; left: 0; right: 0;
    height: 255px;
    display: flex;
    align-items: center;
    justify-content: center;
    padding-top: 30px;
    background: var(--white);
  }
  .back__head .brand-name { color: var(--navy); }
  .back__corner { position: absolute; top: 0; right: 0; }
  .contact-row {
    position: absolute;
    left: 0; right: 0;
    display: flex;
    align-items: center;
    padding: 0 22px 0 26px;
    color: var(--white);
  }
  .contact-row__icon { width: 16px; height: 16px; flex: none; margin-right: 18px; }
  .contact-row__text { flex: 1; font-size: 13.5px; line-height: 1.45; letter-spacing: 0.3px; }
  .contact-row__dash { width: 12px; height: 2px; background: var(--accent); flex: none; }
  .contact-row--name {
    top: 255px; height: 78px;
    background: var(--teal);
  }
  .contact-row--name .contact-row__dash { background: var(--white); }
  .person__name { font-size: 19px; letter-spacing: 0.5px; text-transform: uppercase; }
  .person__name strong { font-weight: 700; }
  .person__name span { font-weight: 300; }
  .person__role { font-size: 10.5px; letter-spacing: 0.8px; text-transform: uppercase; opacity: 0.85; }
  .contact-row--phone { top: 333px; height: 75px; border-bottom: 1px solid var(--rule); }
  .contact-row--web { top: 408px; height: 75px; border-bottom: 1px solid var(--rule); }
  .contact-row--address { top: 483px; height: 77px; }
</style>
</head>
<body>

  <section class="card card--front" aria-label="Business card, side one">
    <div class="front__brand">
      <div class="brand-name"><span class="brand-name__mark"></span>Brightway Haus Inc.</div>
      <p class="front__tagline">Where Shine Counts</p>
    </div>
    <div class="front__footer">
      <p class="front__web">www.thebrightwayhaus.ca</p>
    </div>
  </section>

  <section class="card card--back" aria-label="Business card, side two">
    <div class="back__head">
      <div class="brand-name"><span class="brand-name__mark"></span>Brightway Haus Inc.</div>
    </div>
    <svg class="back__corner" width="120" height="110" viewBox="0 0 120 110" aria-hidden="true">
      <polygon points="40,0 120,0 120,110 100,110" fill="var(--teal)"/>
    </svg>

    <div class="contact-row contact-row--name">
      <svg class="contact-row__icon" viewBox="0 0 16 16" aria-hidden="true">
        <circle cx="8" cy="5" r="3.5" fill="#fff"/>
        <path d="M1.5 16c0-4 3-6.5 6.5-6.5s6.5 2.5 6.5 6.5z" fill="#fff"/>
      </svg>
      <div class="contact-row__text">
        <p class="person__name"><strong>Marlen</strong> <span>Osterby</span></p>
        <p class="person__role">Graphic Designer</p>
      </div>
      <span class="contact-row__dash"></span>
    </div>

    <div class="contact-row contact-row--phone">
      <svg class="contact-row__icon" viewBox="0 0 16 16" aria-hidden="true">
        <path d="M3.6 1.2l2.3 2.8-1.4 1.6c.9 2.1 2.9 4.2 5.9 5.9l1.6-1.4 2.8 2.3-1.6 2.4C7.3 14.6 1.4 8.7 1.2 2.8z" fill="#fff"/>
      </svg>
      <div class="contact-row__text">
        <p>555 . 014 . 2280</p>
        <p>555 . 014 . 2281</p>
      </div>
      <span class="contact-row__dash"></span>
    </div>

    <div class="contact-row contact-row--web">
      <svg class="contact-row__icon" viewBox="0 0 16 16" aria-hidden="true">
        <g fill="none" stroke="#fff" stroke-width="1.3">
          <circle cx="8" cy="8" r="6.8"/>
          <ellipse cx="8" cy="8" rx="3" ry="6.8"/>
          <line x1="1.2" y1="8" x2="14.8" y2="8"/>
        </g>
      </svg>
      <div class="contact-row__text">
        <p>www.thebrightwayhaus.ca</p>
        <p>marlen@mailbox.com</p>
      </div>
      <span class="contact-row__dash"></span>
    </div>

    <div class="contact-row contact-row--address">
      <svg class="contact-row__icon" viewBox="0 0 16 16" aria-hidden="true">
        <path d="M8 1.5L1 8h2v6.5h4v-4h2v4h4V8h2z" fill="#fff"/>
      </svg>
      <div class="contact-row__text">
        <p>42 Larkfield Avenue</p>
        <p>Oregon 97035</p>
      </div>
      <span class="contact-row__dash"></span>
    </div>
  </section>

</body>
</html>
```